Design 4 pages for an event discovery website

This is a contest for the design of 4 pages for an events discovery website. The feature is part of the new sign-up process.

Please see the attached document for a full scope, mockups and the parent category icons.

Target Market(s)

18-35 Australian event goers

Industry/Entity Type

Events

Number of Pages Required

4 page

```html
<!DOCTYPE html>
<html lang="en">
<head>
<meta charset="utf-8">
<title>Kivento – Linking to Other Accounts</title>
<link rel="stylesheet" href="https://fonts.googleapis.com/css2?family=Cabin:wght@400;700&family=Open+Sans:wght@400;600&family=Oswald:wght@500&display=swap">
<style>
  :root {
    --ink: #4a4a4a;
    --muted: #5a5a5a;
    --brand-blue: #5b72b8;
    --signup: #1aa6dc;
    --login: #f2ac2a;
    --btn-one: #3a8fd8;
    --btn-two: #1f5a86;
    --btn-three: #86c021;
    --btn-four: #5870c2;
    --tick: #6aa82a;
    --cross: #e0202a;
    --footer-bg: #141414;
    --footer-text: #c9c9c9;
  }
  * { margin: 0; padding: 0; box-sizing: border-box; }
  html, body { width: 1200px; height: 846px; overflow: hidden; }
  body { position: relative; font-family: "Open Sans", sans-serif; color: var(--ink); background: #fff; }

  .site-header { position: absolute; left: 0; top: 0; width: 1200px; height: 118px; background: rgba(255,255,255,0.94); border-bottom: 1px solid #e4e4e4; z-index: 2; }
  .brand { position: absolute; left: 99px; top: 36px; font-family: "Cabin", sans-serif; font-weight: 700; font-size: 40px; color: var(--ink); letter-spacing: 1px; line-height: 48px; }
  .main-nav { position: absolute; left: 490px; top: 42px; display: flex; }
  .main-nav a { font-family: "Cabin", sans-serif; font-size: 17px; color: var(--ink); text-decoration: none; padding: 0 24px; line-height: 34px; border-right: 1px solid #e8e8e8; }
  .search { position: absolute; left: 698px; top: 41px; width: 190px; height: 36px; border: 1px solid #ddd; border-radius: 3px; background: #fff; font-family: "Cabin", sans-serif; font-size: 14px; color: #999; padding: 0 12px; line-height: 34px; }
  .btn { position: absolute; top: 42px; height: 34px; width: 91px; border-radius: 3px; color: #fff; font-family: "Cabin", sans-serif; font-size: 12.5px; font-weight: 700; text-align: center; line-height: 34px; }
  .btn-signup { left: 907px; background: var(--signup); }
  .btn-login { left: 1010px; background: var(--login); }

  .hero-scene { position: absolute; left: 0; top: 118px; width: 1200px; height: 603px;
    background:
      radial-gradient(ellipse at 45% 35%, rgba(200,170,150,0.55), transparent 45%),
      radial-gradient(ellipse at 85% 55%, rgba(235,235,235,0.8), transparent 40%),
      linear-gradient(180deg, #cfd8dc 0%, #a7c9cf 45%, #d9cdbf 75%, #cdb9a3 100%); }

  .intro-panel { position: absolute; left: 99px; top: 159px; width: 1002px; height: 210px; background: rgba(248,248,248,0.92); border: 1px solid #dadada; text-align: center; }
  .intro-panel h1 { font-family: "Oswald", sans-serif; font-weight: 500; font-size: 58px; color: var(--brand-blue); letter-spacing: -1px; margin-top: 30px; line-height: 66px; }
  .intro-panel p { font-size: 16px; color: var(--muted); line-height: 29px; }
  .intro-panel .lead { margin-top: 22px; }

  .account { position: absolute; left: 99px; width: 206px; height: 57px; border-radius: 2px; color: #fff; display: flex; align-items: center; font-family: "Cabin", sans-serif; font-size: 23px; }
  .account .mark { width: 64px; height: 57px; display: flex; align-items: center; justify-content: center; border-right: 1px solid rgba(0,0,0,0.15); }
  .account .mark span { width: 24px; height: 24px; border-radius: 4px; background: #fff; }
  .account .label { padding-left: 17px; }
  .acc-one { top: 409px; background: linear-gradient(#3f97e0, #2f7fc8); }
  .acc-two { top: 477px; background: linear-gradient(#226592, #1a4f76); }
  .acc-three { top: 546px; background: linear-gradient(#92c827, #78b21a); }
  .acc-four { top: 614px; background: linear-gradient(#607bcc, #4d65b5); }

  .status { position: absolute; left: 335px; display: flex; align-items: center; font-family: "Cabin", sans-serif; font-size: 20px; color: var(--ink); }
  .status svg { margin-right: 14px; }
  .status-linked { top: 422px; }
  .status-pending { top: 562px; }

  .site-footer { position: absolute; left: 0; top: 721px; width: 1200px; height: 125px; background: var(--footer-bg); text-align: center; color: var(--footer-text); }
  .footer-nav { margin-top: 17px; font-size: 12.5px; }
  .footer-nav a { color: var(--footer-text); text-decoration: none; }
  .footer-nav .sep { margin: 0 5px; }
  .copyright { margin-top: 11px; font-size: 12.5px; }
  .social { display: flex; justify-content: center; gap: 5px; margin-top: 11px; }
  .social span { width: 29px; height: 29px; border: 1.5px solid #d0d0d0; border-radius: 50%; }
</style>
</head>
<body>
  <header class="site-header">
    <div class="brand">KIVENTO</div>
    <nav class="main-nav"><a href="#">Find</a><a href="#">Events</a></nav>
    <div class="search">Search</div>
    <div class="btn btn-signup">SIGN UP</div>
    <div class="btn btn-login">LOGIN</div>
  </header>

  <div class="hero-scene" role="img" aria-label="Blurred photo of a person using a laptop on a sunny beach"></div>

  <section class="intro-panel">
    <h1>Linking to Other Accounts</h1>
    <p class="lead">Link in all your other Social Media Account and Music Players</p>
    <p>by Linking your Account, We can save you a lot of time by automatically your intersts</p>
  </section>

  <div class="account acc-one"><div class="mark"><span></span></div><div class="label">Chirpline</div></div>
  <div class="account acc-two"><div class="mark"><span></span></div><div class="label">Snapgrid</div></div>
  <div class="account acc-three"><div class="mark"><span></span></div><div class="label">Tunewave</div></div>
  <div class="account acc-four"><div class="mark"><span></span></div><div class="label">Beatstore</div></div>

  <div class="status status-linked">
    <svg width="20" height="20" viewBox="0 0 20 20" aria-hidden="true"><rect width="20" height="20" rx="3" fill="var(--tick)"/><path d="M4.5 10.5l3.5 3.5 7-8" stroke="#fff" stroke-width="2.6" fill="none" stroke-linecap="round" stroke-linejoin="round"/></svg>
    Linked
  </div>
  <div class="status status-pending">
    <svg width="20" height="20" viewBox="0 0 20 20" aria-hidden="true"><path d="M4 4l12 12M16 4L4 16" stroke="var(--cross)" stroke-width="4" stroke-linecap="round"/></svg>
    We don't have that feature yet but have recarded your interest
  </div>

  <footer class="site-footer">
    <div class="footer-nav"><a href="#">Find</a><span class="sep">/</span><a href="#">Events</a><span class="sep">/</span><a href="#">About Us</a><span class="sep">/</span><a href="#">Search</a><span class="sep">/</span><a href="#">Register</a><span class="sep">/</span><a href="#">Contact Us</a></div>
    <div class="copyright">©2013 - 2014 &nbsp;kivento.com, All Rights Reserved.</div>
    <div class="social"><span></span><span></span><span></span><span></span><span></span></div>
  </footer>
</body>
</html>
```